Podiatry clinic requires a modern revamp and editing of existing website.

I would like a fresh new look and updated information for my current business website. An easy to navigate site with prominent address and phone number for call to action. We are a podiatry clinic that focuses on general and sports podiatry.
I would like 4 pages; including Home page, About Us, Services & Contact.
www.brambleridgepodiatry.net

Target Market(s)

Active working professionals.

Industry/Entity Type

Medical

Coding

Coded - Design and coding required

Number of Pages Required

4 page

Font styles to use
Sans Serif

Colors
6b449b

Requirements
Must have
• A modern look with logo and active images; clean and uncluttered. Visible phone number and address for call to action.
• 4 pages - Home, About Us, Services, Contact.
• Home page - update address & service logos.
• About Us - update of personal information.
• Services - Revamp of existing page.
• Contact page to include Google map, email & phone number.
Nice to have
• Ability to add content easily; eg. a blog or adding video onto Home page.
• Link to Facebook page.

```html
<!DOCTYPE html>
<html lang="en">
<head>
<meta charset="utf-8">
<title>Bramble Ridge Podiatry – Services</title>
<link href="https://fonts.googleapis.com/css2?family=Open+Sans:wght@400;700&family=Raleway:wght@300;400&family=Roboto+Condensed:wght@300;400&display=swap" rel="stylesheet">
<style>
:root{
  --purple:#4a2f96;
  --purple-text:#3f2a8e;
  --green:#7ac142;
  --body:#555;
  --heading:#555;
  --grey-band:#e9e9e9;
  --white:#fff;
  --rule:#5b49a8;
  --hero-top:#c3cfd9;
  --hero-bottom:#8fa9bb;
}
*{box-sizing:border-box;margin:0;padding:0}
html,body{width:1200px;height:3529px;overflow:hidden}
body{font-family:"Open Sans",sans-serif;color:var(--body);background:var(--white);position:relative}

.hero{position:absolute;left:0;top:0;width:1200px;height:678px}
.hero-photo{position:absolute;inset:0;background:linear-gradient(180deg,var(--hero-top) 0%,var(--hero-bottom) 100%)}
.brand{position:absolute;left:78px;top:22px;display:flex;align-items:center;gap:14px}
.brand-dot{width:26px;height:26px;border-radius:50%;background:var(--purple)}
.brand-name{font-weight:700;font-size:30px;line-height:1.05;color:var(--purple);width:200px}
.contact{position:absolute;right:82px;top:42px;font-family:"Roboto Condensed",sans-serif;font-weight:300;color:var(--white);text-align:right}
.contact-line{display:flex;align-items:center;justify-content:flex-end;gap:8px;font-size:19px}
.contact-line + .contact-line{margin-top:26px}
.contact-line strong{font-weight:400;font-size:21px}

.nav{position:absolute;left:0;top:678px;width:1200px;height:59px;background:var(--purple);display:flex;padding-left:78px}
.nav a{display:flex;align-items:center;height:59px;padding:0 32px;color:var(--white);text-decoration:none;font-family:"Raleway",sans-serif;font-size:17px}
.nav a.active{background:var(--green)}

.side-photo{position:absolute;left:0;top:737px;width:153px;height:250px;background:linear-gradient(180deg,#e6d9d3 0%,#d9b3a6 100%)}

.intro{position:absolute;left:0;top:790px;width:1200px;text-align:center}
.section-title{font-family:"Raleway",sans-serif;font-weight:300;font-size:43px;color:var(--heading)}
.section-title span{color:var(--purple-text);font-weight:400}
.intro p{width:720px;margin:14px auto 0;font-size:15px;line-height:24px;color:var(--body)}
.sub-title{font-family:"Raleway",sans-serif;font-weight:300;font-size:33px;color:var(--heading);text-align:center}
.sub-title span{color:var(--purple-text);font-weight:400}
.general-title{position:absolute;left:0;top:958px;width:1200px}

.treatments{position:absolute;left:85px;width:1037px;list-style:none}
.general{top:1000px}
.treatment{height:179px;display:flex;align-items:flex-start;padding-top:20px;border-bottom:1px solid var(--rule)}
.treatment:last-child{border-bottom:none}
.thumb{flex:none;width:134px;height:134px;border-radius:50%;border:2px solid var(--purple)}
.treatment-body{margin-left:31px;padding-top:22px}
.treatment h3{font-size:22px;font-weight:700;color:var(--purple-text);margin-bottom:10px}
.treatment p{font-size:14.5px;line-height:24px;color:var(--body)}

.specialised{position:absolute;left:0;top:2459px;width:1200px;height:1016px;background:var(--grey-band)}
.special-feet{position:absolute;left:906px;top:-24px;width:294px;height:153px;background:linear-gradient(180deg,#eddcd3 0%,#e2bfae 100%)}
.special-title{position:absolute;left:0;top:42px;width:1200px}
.special-list{top:82px}
.special-list .treatment{height:177px}

.footer{position:absolute;left:0;top:3475px;width:1200px;height:54px;background:var(--purple);color:var(--white);display:flex;align-items:center;justify-content:center;font-size:15px}

.t1{background:#e4c4b4}
.t2{background:#8a6a5c}
.t3{background:#e6c3b2}
.t4{background:#e9dcd6}
.t5{background:#b8a8ad}
.t6{background:#e9b8a8}
.t7{background:#f0d5cc}
.t8{background:#8f7f84}
.s1{background:#e6d0c2}
.s2{background:#e5cfc3}
.s3{background:#b98a7a}
.s4{background:#8d8478}
.s5{background:#7e4a66}
</style>
</head>
<body>

<header class="hero">
  <div class="hero-photo" role="img" aria-label="Photo of bare feet resting by the beach"></div>
  <div class="brand">
    <span class="brand-dot"></span>
    <span class="brand-name">Bramble Ridge Podiatry</span>
  </div>
  <div class="contact">
    <div class="contact-line">
      <svg width="16" height="22" viewBox="0 0 16 22"><path d="M8 0a8 8 0 0 0-8 8c0 6 8 14 8 14s8-8 8-14a8 8 0 0 0-8-8zm0 11a3 3 0 1 1 0-6 3 3 0 0 1 0 6z" fill="#fff"/></svg>
      Suite 12 / 58 Harlow Lane Ashbury 3041
    </div>
    <div class="contact-line">
      <svg width="24" height="24" viewBox="0 0 24 24"><circle cx="12" cy="12" r="12" fill="#fff"/><path d="M8 6l2 3-1.4 1.4a8 8 0 0 0 5 5L15 14l3 2-1 2.5c-5 0-10-5-10-10z" fill="#9bb"/></svg>
      CALL US NOW : <strong>1300 555 274</strong>
    </div>
  </div>
</header>

<nav class="nav">
  <a href="#" class="active">HOME</a>
  <a href="#">ABOUT</a>
  <a href="#">SERVICES</a>
  <a href="#">CONTACT</a>
</nav>

<div class="side-photo" role="img" aria-label="Photo of a hand holding a sore heel"></div>

<section class="intro">
  <h1 class="section-title">SERVICES <span>WE PROVIDE</span></h1>
  <p>Podiatrists are trained to diagnose and treat all medical conditions that affect the feet and lower limb. At Bramble Ridge Podiatry we provide treatment for general &amp; Sports Podiatry conditions and various specialised treatments:</p>
</section>

<h2 class="sub-title general-title">General <span>Treatments</span></h2>

<ul class="treatments general">
  <li class="treatment"><div class="thumb t1" role="img" aria-label="Photo of nail treatment"></div><div class="treatment-body"><h3>Nails</h3><p>Nail treatment for difficult to reach feet; ingrown nails; overly thick nails; fungal nails; nails subjected to trauma.</p></div></li>
  <li class="treatment"><div class="thumb t2" role="img" aria-label="Photo of corn treatment"></div><div class="treatment-body"><h3>Corns</h3><p>Corns - hard dry skin lesions due to concentrated pressure from footwear or abnormal foot structure.</p></div></li>
  <li class="treatment"><div class="thumb t3" role="img" aria-label="Photo of callus care"></div><div class="treatment-body"><h3>Callus</h3><p>Callus - areas of dry skin due to pressure or friction, especially around the heels or bony parts of the feet.</p></div></li>
  <li class="treatment"><div class="thumb t4" role="img" aria-label="Photo of a foot being examined for warts"></div><div class="treatment-body"><h3>Warts</h3><p>Warts - also called Papillomas or Verrucae are a viral infection that causes a lesion on the feet. Warts are commonly<br>contracted from public swimming pools and wet tiled surfaces.</p></div></li>
  <li class="treatment"><div class="thumb t5" role="img" aria-label="Photo of skin care on feet"></div><div class="treatment-body"><h3>Skin Disorders</h3><p>Skin Disorders - fungal infections/ tinea/athlete's foot; dermatitis, sweating feet; foot odour; dry cracked skin.</p></div></li>
  <li class="treatment"><div class="thumb t6" role="img" aria-label="Photo of a sore heel"></div><div class="treatment-body"><h3>Heel pain / Heel Spurs / &nbsp;Arch pain</h3><p>Heel pain / Heel Spurs / &nbsp;Arch pain - Plantar Fasciitis - Common condition that causes pain around the heel or arch area<br>that is caused by factors such as faulty foot biomechanics, poor footwear, sports or work activities, injuries and obesity.</p></div></li>
  <li class="treatment"><div class="thumb t7" role="img" aria-label="Photo of a sore ankle"></div><div class="treatment-body"><h3>Ankle pain / Shin splints / Knee pain</h3><p>Ankle pain / Shin splints / Knee pain - faulty foot biomechanics or injuries can cause excessive strain and damage to soft<br>tissues like muscles &amp; tendons or bones &amp; joints./ These can be treated with various physical therapies and orthoses/arch<br>supports.</p></div></li>
  <li class="treatment"><div class="thumb t8" role="img" aria-label="Photo of a foot with a bunion"></div><div class="treatment-body"><h3>Bunions / Hammertoes / Toe deformities</h3><p>Bunions / Hammertoes / Toe deformities - Bony joint deformities can be caused by faulty foot biomechanics and<br>conditions such as Arthritis, Diabetes or Gout. We can help manage pain and prevent these conditions from getting worse<br>with various products that supply padding or support, as well as provide advice on appropriate footwear.</p></div></li>
</ul>

<section class="specialised">
  <div class="special-feet" role="img" aria-label="Photo of crossed bare feet"></div>
  <h2 class="sub-title special-title">Specialised <span>Treatments</span></h2>
  <ul class="treatments special-list">
    <li class="treatment"><div class="thumb s1" role="img" aria-label="Photo of a diabetic foot check"></div><div class="treatment-body"><h3>Diabetic Management</h3><p>Diabetic Management - &nbsp;Assessment of blood supply / circulation with Doppler Ultrasound; assessment of nerve<br>sensation via Vibration Perception and Monofilament Pressure testing. management and prevention of wounds or ulcers.<br>General foot care and footwear advice for diabetic feet.</p></div></li>
    <li class="treatment"><div class="thumb s2" role="img" aria-label="Photo of nail surgery"></div><div class="treatment-body"><h3>Nail Surgery</h3><p>Nail Surgery - Minor surgical procedure for the permanent removal of ingrown toenails under local anaesthesia.</p></div></li>
    <li class="treatment"><div class="thumb s3" role="img" aria-label="Photo of a biomechanical leg assessment"></div><div class="treatment-body"><h3>Biomechanical Assessment</h3><p>Biomechanical Assessment - &nbsp;We are able to help diagnose abnormal foot biomechanics that may be contributing to pain,<br>injury or deformities in the foot and lower limb.</p></div></li>
    <li class="treatment"><div class="thumb s4" role="img" aria-label="Photo of running on a treadmill"></div><div class="treatment-body"><h3>Gait Analysis</h3><p>Gait Analysis - Treadmill analysis of the gait whilst walking or running to ascertain biomechanical problems or<br>abnormalities of movement that may lead to injury or prevent optimal physical performance.</p></div></li>
    <li class="treatment"><div class="thumb s5" role="img" aria-label="Photo of orthotic insoles"></div><div class="treatment-body"><h3>Orthotic Therapy</h3><p>Orthotic Therapy - "Orthoses, or arch supports, are designed to control the function of the foot when there is evidence of<br>faulty biomechanics, such as overly flat or high arched feet or the need to relieve areas of pressure. These may be<br>prefabricated over the counter insoles or custom-made devices.Your podiatrist will assess your foot function and advise<br>which type of device is appropriate for your condition.</p></div></li>
  </ul>
</section>

<footer class="footer">© Bramble Ridge Podiatry- 2016. All Rights Reserved.</footer>

</body>
</html>
```